Business Card for Health Food Store

I need a business card for a health food store that includes the following information.

=========
FRONT
=========

***White background***

Bright Harvest (logo)
Supplements - Health Foods - Remedies

2214 Alder Rd.
Willow Bend, CA 95417
(corner of Ferris Ln.)

707-482-3196

BrightHarvest.co
BrightHarvestGoods@mailbox-example.com

On the right side of the front of the card, use a circle type seal with 25 large in the middle. Put the dates below it.
"Proudly Serving 25 Years Strong"
2001 - 2026

*DO NOT USE A PERSON'S NAME ON THE CARD*

==========
BACK
==========

***Green background***

Full logo in white along with the social logos and handles.

FB Logo / BrightHarvestShop
IG Logo / BrightHarvestShop
Twitter Logo / VisitBrightHarvest

When done I'll need the file in PSD and AI.

Target Market(s)

Surrounding local community

Industry/Entity Type

Retail Health Food Store

Contact Information for Business Card

See brief

Requirements
Must have
• Must be double-sided

```html
<!DOCTYPE html>
<html lang="en">
<head>
<meta charset="utf-8">
<title>Bright Harvest — Business Card</title>
<link rel="stylesheet" href="https://fonts.googleapis.com/css2?family=Poppins:wght@800&family=Oswald:wght@500&family=Arimo:ital@1&display=swap">
<style>
  :root {
    --green: #4cb748;
    --green-deep: #3a9a37;
    --ink: #141414;
    --white: #ffffff;
    --backdrop: #2a2a2a;
  }
  * { box-sizing: border-box; margin: 0; padding: 0; }
  html, body { width: 1200px; height: 900px; overflow: hidden; }
  body {
    background: var(--backdrop);
    display: flex;
    flex-direction: column;
    align-items: center;
    justify-content: center;
    gap: 40px;
  }
  .card {
    position: relative;
    width: 700px;
    height: 400px;
    border-radius: 22px;
    overflow: hidden;
  }
  .card-front { background: var(--white); }
  .card-back { background: var(--green); }
  .card-art { position: absolute; inset: 0; }

  .wordmark {
    font-family: "Poppins", sans-serif;
    font-weight: 800;
    letter-spacing: -0.5px;
    line-height: 1;
  }
  .tagline {
    font-family: "Oswald", sans-serif;
    font-weight: 500;
    text-transform: uppercase;
    letter-spacing: 1px;
  }

  /* front */
  .contact {
    position: absolute;
    left: 52px;
    top: 112px;
    font-family: "Arimo", sans-serif;
    font-style: italic;
    font-size: 17px;
    line-height: 1.32;
    color: var(--ink);
  }
  .contact-address { margin-bottom: 6px; }
  .contact-line { display: flex; align-items: center; gap: 7px; }
  .contact-icon { width: 15px; height: 15px; flex: none; }
  .front-logo {
    position: absolute;
    left: 262px;
    top: 300px;
  }
  .front-logo .wordmark { font-size: 40px; color: var(--ink); display: flex; align-items: center; gap: 10px; }
  .front-logo .mark-dot { width: 22px; height: 22px; border-radius: 50%; background: var(--green); }
  .front-logo .tagline { font-size: 14px; color: var(--green); margin-top: 6px; }

  /* back */
  .back-logo {
    position: absolute;
    left: 0; right: 0;
    top: 118px;
    text-align: center;
    color: var(--white);
  }
  .back-logo .wordmark { font-size: 62px; display: inline-flex; align-items: center; gap: 14px; }
  .back-logo .mark-dot { width: 34px; height: 34px; border-radius: 50%; border: 4px solid var(--white); }
  .back-logo .tagline { font-size: 20px; margin-top: 8px; }
  .socials {
    position: absolute;
    left: 0; right: 0;
    bottom: 52px;
    display: flex;
    justify-content: center;
    gap: 34px;
    list-style: none;
    font-family: "Arimo", sans-serif;
    font-style: italic;
    font-size: 16px;
    color: var(--white);
  }
  .social { display: flex; align-items: center; gap: 8px; }
  .social-icon { width: 20px; height: 20px; border-radius: 50%; border: 2px solid var(--white); }
</style>
</head>
<body>

<section class="card card-front" aria-label="Card front">
  <svg class="card-art" viewBox="0 0 700 400" aria-hidden="true">
    <path d="M0 0 H700 V175 C560 110 360 50 0 40 Z" fill="var(--green)"/>
    <path d="M0 40 C360 50 560 110 700 175" fill="none" stroke="var(--ink)" stroke-width="5"/>
    <path d="M700 235 C660 300 620 350 560 400 H700 Z" fill="var(--green)"/>
    <g class="seal">
      <circle cx="592" cy="196" r="78" fill="var(--green-deep)"/>
      <circle cx="592" cy="196" r="70" fill="none" stroke="var(--white)" stroke-width="2"/>
      <defs>
        <path id="seal-top" d="M537 196 A55 55 0 0 1 647 196"/>
        <path id="seal-bottom" d="M532 202 A60 60 0 0 0 652 202"/>
      </defs>
      <text font-family="Oswald, sans-serif" font-weight="500" font-size="12" letter-spacing="2" fill="var(--white)">
        <textPath href="#seal-top" startOffset="50%" text-anchor="middle">PROUDLY SERVING</textPath>
      </text>
      <text x="592" y="216" text-anchor="middle" font-family="Poppins, sans-serif" font-weight="800" font-size="52" fill="var(--white)">25</text>
      <text x="592" y="232" text-anchor="middle" font-family="Oswald, sans-serif" font-weight="500" font-size="10" letter-spacing="2" fill="var(--white)">YEARS STRONG</text>
      <text font-family="Oswald, sans-serif" font-weight="500" font-size="13" letter-spacing="1" fill="var(--white)">
        <textPath href="#seal-bottom" startOffset="50%" text-anchor="middle">2001 – 2026</textPath>
      </text>
    </g>
  </svg>

  <div class="contact">
    <p class="contact-address">2214 Alder Rd.<br>Willow Bend, CA 95417<br>(corner of Ferris Ln.)</p>
    <p class="contact-line">
      <svg class="contact-icon" viewBox="0 0 16 16" aria-hidden="true"><path d="M4 1 L6 5 L4.5 6.5 C5.5 8.5 7.5 10.5 9.5 11.5 L11 10 L15 12 L13.5 15 C7 14.5 1.5 9 1 2.5 Z" fill="var(--green)"/></svg>
      707-482-3196
    </p>
    <p class="contact-line">
      <svg class="contact-icon" viewBox="0 0 16 16" aria-hidden="true"><rect x="1" y="3" width="14" height="10" fill="var(--green)"/><path d="M1 3 L8 9 L15 3" fill="none" stroke="var(--white)" stroke-width="1.3"/></svg>
      BrightHarvestGoods@mailbox-example.com
    </p>
    <p class="contact-line">
      <svg class="contact-icon" viewBox="0 0 16 16" aria-hidden="true"><circle cx="8" cy="8" r="7" fill="var(--green)"/><path d="M1 8 H15 M8 1 C4 5 4 11 8 15 M8 1 C12 5 12 11 8 15" fill="none" stroke="var(--white)" stroke-width="1"/></svg>
      www.BrightHarvest.co
    </p>
  </div>

  <div class="front-logo">
    <p class="wordmark">Bright Harvest <span class="mark-dot"></span></p>
    <p class="tagline">Supplements • Health Foods • Remedies</p>
  </div>
</section>

<section class="card card-back" aria-label="Card back">
  <div class="back-logo">
    <p class="wordmark">Bright Harvest <span class="mark-dot"></span></p>
    <p class="tagline">Supplements • Health Foods • Remedies</p>
  </div>
  <ul class="socials">
    <li class="social"><span class="social-icon" aria-label="Social network"></span>BrightHarvestShop</li>
    <li class="social"><span class="social-icon" aria-label="Social network"></span>BrightHarvestShop</li>
    <li class="social"><span class="social-icon" aria-label="Social network"></span>VisitBrightHarvest</li>
  </ul>
</section>

</body>
</html>
```